Website art for a private investigator.

The purposed graphic is for a business website ( brellwick.com ). The business name is “Harrowgate & Associates ltd.” This firm is a private investigation agency. The purposed graphic will be placed in the upper most main area of the main page of the website. If you look at the website now there is no graphic.

I have an idea of what I am looking for. I imagine a graphic depicting a contemporary private investigator walking through a dark alley searching for some unknown item. This is symbolic of private investigators hired to find information for people who their selfs do not have the know how nor could they handle the complexity and high stress environment. When I say contemporary I am referring to todays private investigators typically highly educated and well dressed.

Target Market(s)

People who need a private investigator

Industry/Entity Type

Business

Requirements
Must have
• match website; I have an idea of what I am looking for. I imagine a graphic depicting a contemporary private investigator walking through a dark alley searching for some unknown item. This is symbolic of private investigators hired to find information for people who their selfs do not have the know how nor could they handle the complexity and high stress environment. When I say contemporary I am referring to todays private investigators typically highly educated and well dressed.
Should not have
• Everyone please understand, I am not looking for a new website. I am only looking for the image. If you have submitted a design and its displayed on another website other than mine. I will not select your design. I am sorry for being harsh, but I asked for the image to match my website.

```html
<!DOCTYPE html>
<html lang="en">
<head>
<meta charset="utf-8">
<title>Harrowgate &amp; Associates ltd. — Private Investigators</title>
<link rel="stylesheet" href="https://fonts.googleapis.com/css2?family=Raleway:wght@300;400;500&family=Open+Sans:wght@400;600;700&family=Teko:wght@400;500&family=Arimo:wght@400;700&display=swap">
<style>
  :root{
    --brand-blue:#1462ad;
    --footer-blue:#115caa;
    --ink:#222;
    --text-grey:#7a7a7a;
    --light-grey:#9a9a9a;
    --nav-black:#050505;
    --white:#fff;
    --ring:#d4d4d4;
  }
  *{box-sizing:border-box;margin:0;padding:0}
  html,body{width:1200px;height:2270px;overflow:hidden;background:var(--white)}
  body{position:relative;font-family:"Arimo",Arial,sans-serif;color:var(--ink)}
  .abs{position:absolute}

  /* Header */
  .site-header{position:absolute;left:0;top:0;width:1200px;height:126px;background:var(--white)}
  .brand{position:absolute;left:103px;top:27px;display:flex;align-items:center;gap:10px}
  .brand-mark{width:76px;height:76px;border-radius:50%;background:var(--ink)}
  .brand-name{font-family:"Open Sans",sans-serif;font-weight:700;color:var(--brand-blue);font-size:27px;line-height:30px}
  .call{position:absolute;right:103px;top:42px;font-family:"Open Sans",sans-serif;font-size:32px;color:#333;letter-spacing:.5px}
  .call span{color:var(--brand-blue);letter-spacing:1px}

  /* Nav */
  .main-nav{position:absolute;left:0;top:126px;width:1200px;height:53px;background:var(--nav-black)}
  .nav-list{position:absolute;left:110px;top:0;height:53px;display:flex;align-items:center;gap:36px;list-style:none;color:var(--white);font-family:"Open Sans",sans-serif;font-size:15px;letter-spacing:1.2px}
  .social{position:absolute;right:108px;top:18px;display:flex;gap:16px}
  .social i{display:block;width:14px;height:14px;border-radius:50%;background:#6a6a6a}

  /* Hero */
  .hero{position:absolute;left:0;top:179px;width:1200px;height:457px;
    background:radial-gradient(ellipse at 60% 30%,#6e6e6e 0%,#3a3a3a 35%,#141414 80%),#1a1a1a}

  /* Services */
  .section-title{font-family:"Raleway",sans-serif;font-weight:300;font-size:29px;letter-spacing:1px;text-align:center;color:#333}
  .section-title b{font-weight:500}
  .services-title{position:absolute;left:0;top:684px;width:1200px}
  .services-lead{position:absolute;left:150px;top:728px;width:900px;text-align:center;font-size:15.5px;line-height:24px;color:#222}
  .service{position:absolute;top:830px;display:flex;gap:12px}
  .service-photo{width:150px;height:150px;border-radius:50%;border:2px solid var(--ring);padding:6px;flex:none}
  .service-photo div{width:100%;height:100%;border-radius:50%}
  .service h3{font-family:"Teko",sans-serif;font-weight:400;color:var(--brand-blue);font-size:31px;line-height:25px;margin-top:16px}
  .service p{font-size:12.5px;line-height:15px;color:var(--light-grey);width:150px;margin-top:10px}

  /* What we do */
  .about-band{position:absolute;left:0;top:1100px;width:1200px;height:310px;
    background:radial-gradient(ellipse at 50% 40%,#fafafa 0%,#efefef 60%,#e6e6e6 100%);border-bottom:3px solid #eaeaea}
  .about-title{position:absolute;left:0;top:54px;width:1200px}
  .about-text{position:absolute;left:120px;top:106px;width:960px;text-align:center;font-size:14.5px;line-height:24.5px;color:#777}
  .btn{position:absolute;left:505px;top:225px;width:173px;height:48px;background:var(--brand-blue);color:var(--white);font-size:14px;display:flex;align-items:center;justify-content:center}

  /* Fees & testimonials */
  .h2{font-family:"Raleway",sans-serif;font-size:23px;font-weight:400;color:#333;line-height:29px}
  .fees{position:absolute;left:110px;top:1472px;width:540px}
  .fees .sub{font-size:15.5px;color:#333;margin-top:9px}
  .fees p.body{font-size:14.5px;line-height:22px;color:var(--text-grey);margin-top:10px}
  .fees p.body + p.body{margin-top:22px}
  .testimonials{position:absolute;left:762px;top:1468px;width:340px}
  .quote{position:absolute;left:0;display:flex}
  .avatar{width:68px;height:68px;border-radius:50%;flex:none;margin-top:2px}
  .quote-body{margin-left:22px;padding-left:16px;border-left:1px solid #e2e2e2;width:250px}
  .quote-body p{font-size:14.5px;line-height:22px;color:var(--text-grey)}
  .quote-body cite{display:block;font-style:normal;font-size:14px;color:var(--text-grey);margin-top:10px}
  .quote-body cite b{color:#444}

  /* Footer */
  .site-footer{position:absolute;left:0;top:1918px;width:1200px;height:303px;background:var(--footer-blue);color:var(--white)}
  .footer-brand{position:absolute;left:96px;top:68px;width:212px;text-align:center}
  .footer-brand .mark{width:74px;height:74px;border-radius:50%;background:var(--white);margin:0 auto 12px}
  .footer-brand .name{font-family:"Open Sans",sans-serif;font-weight:700;font-size:25px;line-height:28px;color:var(--white)}
  .col{position:absolute;top:48px}
  .col h4{font-family:"Open Sans",sans-serif;font-size:17.5px;font-weight:600;letter-spacing:.3px}
  .col ul{list-style:none;margin-top:14px;font-size:15.5px;line-height:24px}
  .col address{font-style:normal;font-size:16.5px;line-height:24px;margin-top:14px}
  .col address small{font-size:12px;letter-spacing:.5px}
  .divider{position:absolute;top:44px;height:210px;border-left:1px dotted rgba(255,255,255,.55)}
  .map{position:absolute;left:800px;top:87px;width:302px;height:135px;border:4px solid #e9e9e9;background:linear-gradient(135deg,#dfe3d8,#ecebe4 60%,#d9e2cf)}
  .copyright{position:absolute;left:0;top:2221px;width:1200px;height:49px;background:#000;color:var(--white);font-size:14px;display:flex;align-items:center;justify-content:center}
</style>
</head>
<body>

<header class="site-header">
  <div class="brand">
    <div class="brand-mark"></div>
    <div class="brand-name">HARROWGATE &amp;<br>Associates ltd.</div>
  </div>
  <div class="call"><span>CALL</span> 555.014.229</div>
</header>

<nav class="main-nav">
  <ul class="nav-list">
    <li>MAIN</li><li>|</li><li>INVESTIGATION &amp; ANNALYSIS</li><li>|</li><li>NEWS</li><li>|</li><li>FEES</li>
  </ul>
  <div class="social"><i></i><i></i><i></i><i></i><i></i><i></i></div>
</nav>

<section class="hero" role="img" aria-label="Well-dressed investigator with glasses, coat over arm and briefcase, walking through a dark wet brick alley at night"></section>

<section>
  <h2 class="section-title services-title">HARROWGATE <b>SERVICES</b></h2>
  <p class="services-lead">Sed ut perspiciatis unde omnis iste natus error sit voluptatem accusantium doloremque laudantium,totam rem aperiam,<br>eaque ipsa quae ab illo inventore veritatis et quasi architecto beatae vitae dicta.</p>

  <div class="service" style="left:105px">
    <div class="service-photo"><div role="img" aria-label="Close-up of hands in handcuffs" style="background:radial-gradient(circle,#d9a08a,#9c5a4a)"></div></div>
    <div><h3>Criminal<br>Defense</h3><p>Sed ut perspiciatis unde omnis iste natus error sit voluptatem accusantium doloremque laudantiu totam remeriam.</p></div>
  </div>
  <div class="service" style="left:446px">
    <div class="service-photo"><div role="img" aria-label="Hand holding a magnifying glass over a document" style="background:radial-gradient(circle,#f1ece6,#c9a58a)"></div></div>
    <div><h3>Legal<br>Investigation</h3><p>Sed ut perspiciatis unde omnis iste natus error sit voluptatem accusantium doloremque laudantiu totam remeriam.</p></div>
  </div>
  <div class="service" style="left:790px">
    <div class="service-photo"><div role="img" aria-label="Photographer with a camera in dramatic black and white light" style="background:radial-gradient(circle,#8a8a8a,#111)"></div></div>
    <div><h3>Forensic<br>Photography</h3><p>Sed ut perspiciatis unde omnis iste natus error sit voluptatem accusantium doloremque laudantiu totam remeriam.</p></div>
  </div>
</section>

<section class="about-band">
  <h2 class="section-title about-title">WHAT WE DO <b>HARROWGATE</b></h2>
  <p class="about-text">Lorem Ipsum is simply dummy text of the printing and typesetting industry. Lorem Ipsum has been the industry's standard dummy text ever since the 1500s, when an unknown printer took a galley of type and scrambled it to make a type specimen book. It has survived not only five centuries, but also the leap into electronic typesetting, remaining essentially unchanged. It was popularised in the 1960s with the including versions of Lorem Ipsum.</p>
  <div class="btn">Read More</div>
</section>

<section class="fees">
  <h2 class="h2">How Much Do We Charge</h2>
  <p class="sub">Sed ut perspiciatis unde omnis iste natus error sit voluptatem.</p>
  <p class="body">We believe the services of a private investigator should be obtainable and reasonable to the general public. The fees charged by Harrowgate &amp; Associates are low compared to other similar firms. For one, we do not charge for travel. This makes us available to you without unnecessary expense. Investigative and analysis services are available by the hour or at a flat rate. See the private investigator fees for more information.</p>
  <p class="body">Our investigative and analysis ability is based on the application of Structured Analysis and Expert Judgement. The use of these methods allows us to provide clients of Harrowgate &amp; Associates with objective results. In the areas of reconstructing past events, evaluating the credibility of evidence and witness testimony, processing of abstract information derived from multiple portals, and making analytical judgements based on available subject matter information. In turn, we are not only able to provide investigative service, but full analysis support to clients.</p>
</section>

<section class="testimonials">
  <h2 class="h2">Ohio and West Virginia Private Investigators</h2>
  <div class="quote" style="top:84px">
    <div class="avatar" role="img" aria-label="Client portrait" style="background:radial-gradient(circle,#8b5a48,#2a1a16)"></div>
    <div class="quote-body"><p>Lorem ipsum dolor sit amet, consectetur adipisicing elit, sed do eiusmod tempor incididunt</p><cite><b>-John Doe/</b> Director of veltrana.com</cite></div>
  </div>
  <div class="quote" style="top:198px">
    <div class="avatar" role="img" aria-label="Client portrait" style="background:radial-gradient(circle,#e8d4e8,#8a6a9a)"></div>
    <div class="quote-body"><p>Lorem ipsum dolor sit amet, consectetur adipisicing elit, sed do eiusmod tempor incididunt</p><cite><b>-John Doe/</b> Director of veltrana.com</cite></div>
  </div>
  <div class="quote" style="top:316px">
    <div class="avatar" role="img" aria-label="Client portrait" style="background:radial-gradient(circle,#c49a7a,#3a2a22)"></div>
    <div class="quote-body"><p>Lorem ipsum dolor sit amet, consectetur adipisicing elit, sed do eiusmod tempor incididunt</p><cite><b>-John Doe/</b> Director of veltrana.com</cite></div>
  </div>
</section>

<footer class="site-footer">
  <div class="footer-brand">
    <div class="mark"></div>
    <div class="name">HARROWGATE &amp;<br>Associates ltd.</div>
  </div>
  <div class="col" style="left:368px">
    <h4>LINKS</h4>
    <ul><li>Labor Dispute</li><li>Accidents</li><li>Negligence</li><li>Employment Accident</li><li>Product Liability</li><li>Equity Matters</li><li>Missing Person</li></ul>
  </div>
  <div class="divider" style="left:528px"></div>
  <div class="col" style="left:551px">
    <h4>CONTACT US</h4>
    <address>HARROWGATE <small>ASSOCIATES</small><br>P.O. Box 412<br>Millbrook, Ohio 45091<br><br>&nbsp;Phone: (555) 014-2290<br>&nbsp;Fax: (555) 014-2290</address>
  </div>
  <div class="divider" style="left:766px"></div>
  <div class="col" style="left:808px"><h4>HOW TO FIND US?</h4></div>
  <div class="map" role="img" aria-label="Street map showing the office location"></div>
</footer>

<div class="copyright">© 2012-2014 Harrowgate &amp; Associates ltd. All rights resesrved.</div>

</body>
</html>
```